Meadow Kr Circle (company name is Meadow Kr Circle LLP)

management of homestay, hospitality something similar with https://www.dorvika.example

Target Market(s)

johor bahru market (Malaysia)

Contact Information for Business Card

Meadow Circle KR LLP

Logo Text

eyes catching, attractive, amazing, Nice, jaw dropping for design

Coding

Coded - Design and coding required

Number of Pages Required

5+ page

Colors

Designer to choose colors to be used in the design.

Requirements
Must have
• please change the short term proposal to our company logo and change the name from dorvika to meadow KR Circle LLP
• thanks
Nice to have
• please let me have eyes catching , jaw dropping design

```html
<!DOCTYPE html>
<html lang="en">
<head>
<meta charset="utf-8">
<title>Meadow Kr Circle — Short-stay Management</title>
<link rel="stylesheet" href="https://fonts.googleapis.com/css2?family=Poppins:wght@400;500;600;700&display=swap">
<style>
:root{
  --teal:#0f7d87;
  --teal-dark:#0b5f67;
  --coral:#f4606b;
  --ink:#2b2b2b;
  --muted:#555;
  --line:#dcdcdc;
  --soft:#f2f2f2;
  --white:#fff;
  --footer:#2f3230;
}
*{box-sizing:border-box;margin:0;padding:0}
html,body{width:1200px;height:3913px;overflow:hidden}
body{font-family:'Poppins',sans-serif;color:var(--ink);background:var(--white);position:relative}
.abs{position:absolute}

/* header */
.site-header{position:absolute;left:0;top:0;width:1200px;height:180px;background:var(--white)}
.contact-block{position:absolute;top:38px;display:flex;gap:14px;font-size:14.5px;line-height:23px;color:var(--ink)}
.contact-block svg{flex:none;margin-top:2px}
.contact-left{left:112px}
.contact-right{left:810px}
.brand{position:absolute;left:0;width:1200px;top:32px;text-align:center}
.brand-mark{display:block;width:44px;height:44px;border-radius:50%;border:3px solid var(--coral);margin:0 auto 8px}
.brand-name{font-size:17px;font-weight:700;color:var(--teal);letter-spacing:.5px}
.main-nav{position:absolute;left:112px;top:125px;width:976px;height:55px;border-top:1px solid var(--line);display:flex;justify-content:space-between;align-items:center;padding:0 20px}
.main-nav a{font-size:15.5px;font-weight:500;color:var(--ink);text-decoration:none;padding:0 4px}
.main-nav .sep{width:1px;height:28px;background:var(--line)}

/* hero */
.hero{position:absolute;left:0;top:180px;width:1200px;height:517px}
.hero-photo{position:absolute;inset:0;background:linear-gradient(100deg,#d8d6d1 0%,#8b8a86 35%,#4a4847 60%,#2d2c2b 100%)}
.hero-shade{position:absolute;inset:0;background:linear-gradient(90deg,rgba(0,0,0,.35),rgba(0,0,0,0) 55%)}
.hero-title{position:absolute;left:112px;top:117px;font-size:44px;font-weight:600;color:var(--white);letter-spacing:.5px}
.hero-sub{position:absolute;left:112px;top:190px;font-size:20px;line-height:32px;color:var(--white)}
.btn-ghost{position:absolute;left:112px;top:290px;width:112px;height:49px;border:2px solid var(--white);color:var(--white);font-size:16px;display:flex;align-items:center;justify-content:center}
.hero-dots{position:absolute;left:112px;top:375px;display:flex;gap:6px}
.hero-dots span{width:11px;height:11px;border-radius:50%;background:rgba(255,255,255,.55)}
.hero-dots span:first-child{background:var(--white)}

/* about */
.about{position:absolute;left:0;top:697px;width:1200px;height:555px;background:var(--white)}
.section-heading{font-size:30px;font-weight:600;color:var(--teal)}
.heading-rule{width:86px;height:3px;background:var(--teal);margin-top:10px}
.about-text{position:absolute;left:112px;top:110px;width:570px}
.about-text p{font-size:14.5px;line-height:25px;color:var(--muted);margin-top:28px}
.about-text p + p{margin-top:22px}
.btn-coral{display:inline-flex;align-items:center;justify-content:center;background:var(--coral);color:var(--white);font-size:16px;width:112px;height:50px;margin-top:30px}
.about-frame{position:absolute;left:770px;top:70px;width:316px;height:337px;border:3px solid var(--teal)}
.about-photo{position:absolute;left:757px;top:60px;width:316px;height:337px;background:linear-gradient(135deg,#caa66a,#8a6a44 45%,#3a2f28);border:6px solid var(--white);box-shadow:0 2px 8px rgba(0,0,0,.2)}

/* services */
.services{position:absolute;left:0;top:1252px;width:1200px;height:632px;background:var(--soft)}
.centered-heading{position:absolute;left:0;width:1200px;text-align:center}
.centered-heading .heading-rule{margin:14px auto 0}
.service-card{position:absolute;top:188px;width:381px;height:355px;overflow:hidden}
.service-card .photo{position:absolute;inset:0}
.service-card h3{position:absolute;left:16px;top:228px;font-size:16px;font-weight:500;color:var(--white)}
.service-card p{position:absolute;left:16px;top:260px;width:350px;font-size:13.5px;line-height:23px;color:var(--white);text-align:justify}
.card-enquiry{left:13px}.card-enquiry .photo{background:linear-gradient(165deg,#f0424f 0%,#c73a45 45%,#1d8b91 100%)}
.card-cleaning{left:410px}.card-cleaning .photo{background:linear-gradient(170deg,#127e86 0%,#2a8f8e 40%,#e8505c 100%)}
.card-marketing{left:806px}.card-marketing .photo{background:linear-gradient(165deg,#f36a72 0%,#e0787c 45%,#2a9aa0 100%)}

/* steps */
.steps{position:absolute;left:0;top:1884px;width:1200px;height:600px;background:var(--white)}
.steps-intro{position:absolute;left:0;width:1200px;top:162px;text-align:center;font-size:15px;color:var(--muted)}
.step{position:absolute;top:240px;width:250px;text-align:center}
.step svg{display:block;margin:0 auto}
.step h4{font-size:16.5px;font-weight:500;line-height:26px;margin-top:14px}
.step.teal h4{color:var(--teal)}
.step.coral h4{color:var(--coral)}

/* blog */
.blog{position:absolute;left:0;top:2484px;width:1200px;height:1208px;background:var(--soft)}
.post{position:absolute;left:112px;width:976px;height:269px;background:var(--white);box-shadow:0 1px 6px rgba(0,0,0,.12)}
.post .thumb{position:absolute;left:11px;top:11px;width:294px;height:247px}
.post h3{position:absolute;left:326px;top:36px;font-size:21px;font-weight:500;color:var(--teal)}
.post time{position:absolute;left:326px;top:106px;font-size:14px;color:var(--coral)}
.post p{position:absolute;left:326px;top:140px;width:620px;font-size:13.5px;line-height:24px;color:var(--ink);text-align:justify}
.post .btn-small{position:absolute;left:326px;top:190px;width:93px;height:40px;background:var(--coral);color:var(--white);font-size:13.5px;display:flex;align-items:center;justify-content:center}
.thumb-1{background:linear-gradient(135deg,#9a9a96,#4c4c4a 60%,#2a2a2a)}
.thumb-2{background:linear-gradient(135deg,#d9b48a,#a87450 50%,#5b3b2a)}
.thumb-3{background:linear-gradient(135deg,#c9a870,#7a6650 50%,#3d3630)}
.pagination{position:absolute;left:0;width:1200px;top:1104px;display:flex;justify-content:center;align-items:center;gap:12px}
.page{width:34px;height:34px;border-radius:50%;border:2px solid var(--teal);color:var(--teal);font-size:16px;display:flex;align-items:center;justify-content:center}
.page.current{background:var(--teal);color:var(--white)}

/* footer */
.site-footer{position:absolute;left:0;top:3692px;width:1200px;height:221px}
.footer-photo{position:absolute;inset:0;background:linear-gradient(90deg,#3d403c,#2a2d2b 50%,#3a3c39)}
.footer-brand{position:absolute;left:112px;top:62px;display:flex;align-items:center;gap:12px}
.footer-brand .brand-mark{margin:0;border-color:var(--white)}
.footer-brand .brand-name{color:var(--white);font-size:20px}
.footer-address{position:absolute;left:810px;top:57px;display:flex;gap:12px;color:var(--white);font-size:14px;line-height:23px}
.footer-rule{position:absolute;left:522px;top:140px;width:566px;height:1px;background:rgba(255,255,255,.7)}
.copyright{position:absolute;left:700px;top:164px;font-size:13.5px;color:var(--white)}
</style>
</head>
<body>

<header class="site-header">
  <div class="contact-block contact-left">
    <svg width="22" height="28" viewBox="0 0 22 28"><path d="M11 2a8.5 8.5 0 0 0-8.5 8.5C2.5 17 11 26 11 26s8.5-9 8.5-15.5A8.5 8.5 0 0 0 11 2z" fill="none" stroke="#f4606b" stroke-width="2.2"/><circle cx="11" cy="10.5" r="3.2" fill="none" stroke="#f4606b" stroke-width="2.2"/></svg>
    <div>Unit 12-03 Lumen Court, Jalan Seri Ara,<br>Taman Lantana, 80450 Johor Bahru.</div>
  </div>
  <div class="brand">
    <span class="brand-mark"></span>
    <span class="brand-name">MEADOW KR CIRCLE</span>
  </div>
  <div class="contact-block contact-right">
    <svg width="30" height="30" viewBox="0 0 30 30"><path d="M7 3l5 6-3 3c1.5 3.5 4.5 6.5 8 8l3-3 6 5-3 4C13 25 5 17 3 7z" fill="none" stroke="#f4606b" stroke-width="2.2" stroke-linejoin="round"/></svg>
    <div>Aria Tan | +65 9000 1234<br>Marketing &amp; Operations Manager</div>
  </div>
  <nav class="main-nav">
    <a>Home</a><span class="sep"></span>
    <a>Explore The Place</a><span class="sep"></span>
    <a>Hospitality Service</a><span class="sep"></span>
    <a>Blog</a><span class="sep"></span>
    <a>Our Story</a><span class="sep"></span>
    <a>Let's Talk</a><span class="sep"></span>
    <a>Contact Us</a>
  </nav>
</header>

<section class="hero">
  <div class="hero-photo" role="img" aria-label="Modern serviced apartment living room with grey sofa, patterned wallpaper and wall-mounted TV"></div>
  <div class="hero-shade"></div>
  <h1 class="hero-title">MEADOW KR CIRCLE</h1>
  <p class="hero-sub">Short-stay Management Proposal.<br>Maximize your rental income.</p>
  <a class="btn-ghost">Read More</a>
  <div class="hero-dots"><span></span><span></span><span></span><span></span><span></span></div>
</section>

<section class="about">
  <div class="about-text">
    <h2 class="section-heading">About Us</h2>
    <div class="heading-rule"></div>
    <p>We are a short-term rental management and provides hospitality services to help property owners maximise their rental income.</p>
    <p>Our goal is to help you reap the most from your rental income without you having to do any of the hard work such as handle all the particular renting problems on Staynook, Roomharbor.example, cleaning and dealing with tenants and guests.</p>
    <a class="btn-coral">Read More</a>
  </div>
  <div class="about-frame"></div>
  <div class="about-photo" role="img" aria-label="Smiling guests receiving keys at a hotel reception desk"></div>
</section>

<section class="services">
  <div class="centered-heading" style="top:68px">
    <h2 class="section-heading">Our Hassle-Free Full Hospitality Service</h2>
    <div class="heading-rule"></div>
  </div>
  <article class="service-card card-enquiry">
    <div class="photo" role="img" aria-label="Hotel concierge greeting guests at check-in"></div>
    <h3>Answering Enquiries, Check-Ins / Outs</h3>
    <p>We will answer all guest's enquiries, meet them to handover key and verification check. We also provide 24hr on-call support.</p>
  </article>
  <article class="service-card card-cleaning">
    <div class="photo" role="img" aria-label="Housekeeper making a bed with fresh linen"></div>
    <h3>Cleaning, Laundry and Maintenance</h3>
    <p>We get the professional cleaning team to clean up the place after the guest checked-out every time.</p>
  </article>
  <article class="service-card card-marketing">
    <div class="photo" role="img" aria-label="Hands working on a laptop and paperwork"></div>
    <h3>Marketing &amp; Optimization</h3>
    <p>We take professional photos and write persuasive copywriting to optimize your listing in order to get more booking.</p>
  </article>
</section>

<section class="steps">
  <div class="centered-heading" style="top:88px">
    <h2 class="section-heading">How To Start?</h2>
    <div class="heading-rule"></div>
  </div>
  <p class="steps-intro">The following steps are required in order to get your place ready to start.</p>

  <div class="step teal" style="left:89px">
    <svg width="190" height="180" viewBox="0 0 190 180"><circle cx="95" cy="90" r="84" fill="none" stroke="#0f7d87" stroke-width="5"/><circle cx="165" cy="42" r="12" fill="#fff" stroke="#0f7d87" stroke-width="5"/>
      <g fill="none" stroke="#0f7d87" stroke-width="4"><rect x="62" y="62" width="14" height="46"/><rect x="80" y="56" width="14" height="52"/><path d="M98 66l10-4 12 44-10 3z"/><path d="M54 112h70"/></g>
      <text x="150" y="112" font-family="Poppins,sans-serif" font-size="46" fill="#0f7d87">1</text></svg>
    <h4>Getting The Required<br>Items</h4>
  </div>
  <div class="step coral" style="left:339px">
    <svg width="190" height="180" viewBox="0 0 190 180"><circle cx="95" cy="90" r="84" fill="none" stroke="#f4606b" stroke-width="5"/><circle cx="165" cy="42" r="12" fill="#fff" stroke="#f4606b" stroke-width="5"/>
      <path d="M62 88l33-28 33 28" fill="none" stroke="#f4606b" stroke-width="5"/><path d="M70 86v30h50V86L95 66z" fill="#f4606b"/><rect x="88" y="98" width="14" height="18" fill="#fff"/>
      <text x="150" y="112" font-family="Poppins,sans-serif" font-size="46" fill="#f4606b">2</text></svg>
    <h4>Renovation &amp;<br>Furnishing</h4>
  </div>
  <div class="step teal" style="left:592px">
    <svg width="190" height="180" viewBox="0 0 190 180"><circle cx="95" cy="90" r="84" fill="none" stroke="#0f7d87" stroke-width="5"/><circle cx="165" cy="42" r="12" fill="#fff" stroke="#0f7d87" stroke-width="5"/>
      <g fill="none" stroke="#0f7d87" stroke-width="4"><path d="M68 56h42l12 12v52H68z"/><path d="M78 72h6M90 72h22M78 84h6M90 84h22M78 96h6M90 96h22M78 108h6M90 108h22"/></g>
      <text x="150" y="112" font-family="Poppins,sans-serif" font-size="46" fill="#0f7d87">3</text></svg>
    <h4>Sign a management<br>agreement</h4>
  </div>
  <div class="step coral" style="left:843px">
    <svg width="190" height="180" viewBox="0 0 190 180"><circle cx="95" cy="90" r="84" fill="none" stroke="#f4606b" stroke-width="5"/><circle cx="165" cy="42" r="12" fill="#fff" stroke="#f4606b" stroke-width="5"/>
      <g fill="none" stroke="#f4606b" stroke-width="4"><rect x="58" y="62" width="64" height="38" rx="3"/><rect x="66" y="70" width="16" height="12"/><path d="M90 74h24M90 84h16"/><circle cx="72" cy="114" r="6"/><path d="M78 114h40M110 114v8M118 114v6"/></g>
      <text x="150" y="112" font-family="Poppins,sans-serif" font-size="46" fill="#f4606b">4</text></svg>
    <h4>Handover Keys &amp; Access<br>cards, and relevant<br>information</h4>
  </div>
</section>

<section class="blog">
  <div class="centered-heading" style="top:60px">
    <h2 class="section-heading">Recent Blog Posts</h2>
    <div class="heading-rule"></div>
  </div>
  <article class="post" style="top:190px">
    <div class="thumb thumb-1" role="img" aria-label="Guests checking in at a hotel front desk"></div>
    <h3>Higher Rental Income Potential</h3>
    <time>May 10, 2018</time>
    <p>We distribute across popular OTA(Online Travel Agency), Staynook, Roomharbor.example etc to maximize your income.</p>
    <a class="btn-small" style="top:188px">Read More</a>
  </article>
  <article class="post" style="top:482px">
    <div class="thumb thumb-2" role="img" aria-label="Family arriving at a holiday home reception"></div>
    <h3>Immediate Monthly Income</h3>
    <time>May 10, 2018</time>
    <p>No worry of late payment from long-term rental, payout are immediately process when guest check-out.</p>
    <a class="btn-small" style="top:188px">Read More</a>
  </article>
  <article class="post" style="top:775px">
    <div class="thumb thumb-3" role="img" aria-label="Traveller with suitcase walking through a hotel lobby"></div>
    <h3>Owner Get 10-nights FREE Stay Per Annum</h3>
    <time>May 10, 2018</time>
    <p>Owner are welcome to stay at their own unit monthly. *No bring forward. We use professional cleaning service to ensure your place.</p>
    <a class="btn-small" style="top:188px">Read More</a>
  </article>
  <nav class="pagination">
    <svg width="30" height="24" viewBox="0 0 30 24"><path d="M28 12H4M13 3l-9 9 9 9" fill="none" stroke="#0f7d87" stroke-width="3.5"/></svg>
    <span class="page current">1</span><span class="page">2</span><span class="page">3</span>
    <svg width="30" height="24" viewBox="0 0 30 24"><path d="M2 12h24M17 3l9 9-9 9" fill="none" stroke="#0f7d87" stroke-width="3.5"/></svg>
  </nav>
</section>

<footer class="site-footer">
  <div class="footer-photo" role="img" aria-label="Dimmed interior of a furnished apartment"></div>
  <div class="footer-brand">
    <span class="brand-mark"></span>
    <span class="brand-name">MEADOW KR CIRCLE</span>
  </div>
  <div class="footer-address">
    <svg width="22" height="28" viewBox="0 0 22 28"><path d="M11 2a8.5 8.5 0 0 0-8.5 8.5C2.5 17 11 26 11 26s8.5-9 8.5-15.5A8.5 8.5 0 0 0 11 2z" fill="none" stroke="#fff" stroke-width="2.2"/><circle cx="11" cy="10.5" r="3.2" fill="none" stroke="#fff" stroke-width="2.2"/></svg>
    <div>Unit 12-03 Lumen Court, Jalan Seri Ara,<br>Taman Lantana, 80450 Johor Bahru.</div>
  </div>
  <div class="footer-rule"></div>
  <p class="copyright">Copyrights @ 2018 Meadow Kr Circle. All Rights Reserved.</p>
</footer>

</body>
</html>
```